Emerging automotive detailing business

I am starting a small automotive detailing business in hopes of becoming a well-known detailer to work on high end cars. I would like a card to reflect the high quality and time I put into my work. The name of the company is Bright Crest Detailing. I feel like it represents racecars getting off the line at the drag strip as well as an innuendo of "Up the Ladder". I do minor paint correction such as clay barring, multi-step buffing and polishing, waxing, hand washes, etc. I am always striving to learn more and improve my work. My goal is to have total customer satisfaction. This is a female run business but I do not want it to be very girly. Elegant is okay! I have pictures of my personal wrenfield attached, they do not need to be incorporated but if you can think of a cool way to use 1 or all of them, go for it!

Target Market(s)

Anyone that owns a vehicle. Preferably high end vehicles such as Valtori, Castellverde and Morvani but I will also happily work on any car, truck or suv no matter what brand.

Industry/Entity Type

Automotive

Contact Information for Business Card

Bright Crest Detailing
Mira Tolland
4175 Quenhollow Rd
Ashmere PA 17492
Cell phone- call/text- 717-555-0148
email- brightcrestdetails@maildrop-example.com
Instagram: @brightcrestdetailing
Facebook: facebook.com/brightcrestdetailing

Requirements
Must have
• Business name, my name, address, phone number. Listing that I do minor paint correction such as clay barring, multi-step buffing and polishing, waxing, hand washes, interior cleaning, and more. (This last part was in nice to haves but I have realized that I do really want it, so I moved it to must haves.) I want something that is different and eye-catching to my customers. Some people have done this very well with cards already submitted to me, but a lot have not. I didn't mess with the "look and feel bars" much because because I am pretty open to the overall design as long as it is not your basic run of the mill design.
Nice to have
• Something car related. Maybe an appointment time/date line. I do not have a logo, but if you would like to design one and incorporate it, that would be amazing!
Should not have
• Purple and Pink colors. Boring, basic, normal card.

```html
<!DOCTYPE html>
<html lang="en">
<head>
<meta charset="utf-8">
<title>Bright Crest Detailing – Business Card</title>
<link href="https://fonts.googleapis.com/css2?family=Open+Sans:wght@400;600;700&display=swap" rel="stylesheet">
<style>
  :root {
    --red: #e01f26;
    --black: #111111;
    --white: #ffffff;
    --ink: #1a1a1a;
    --muted: #444444;
    --backdrop: #ecebe9;
  }
  * { box-sizing: border-box; margin: 0; padding: 0; }
  html, body { width: 1200px; height: 900px; overflow: hidden; }
  body {
    background: var(--backdrop);
    font-family: "Open Sans", Arial, sans-serif;
    position: relative;
  }
  .card {
    position: absolute;
    background: var(--white);
    overflow: hidden;
    box-shadow: 0 6px 18px rgba(0,0,0,0.18);
  }
  .card-front { left: 78px; top: 35px; width: 587px; height: 362px; }
  .card-back { left: 388px; top: 505px; width: 567px; height: 352px; }

  .front-shapes { position: absolute; inset: 0; }

  .brand {
    position: absolute;
    display: flex;
    flex-direction: column;
    align-items: flex-end;
  }
  .brand-row { display: flex; align-items: center; gap: 6px; }
  .brand-mark {
    border-radius: 50%;
    background: var(--red);
    box-shadow: inset 0 0 0 3px var(--red), inset 0 0 0 5px var(--white);
  }
  .brand-name { font-weight: 400; letter-spacing: 2px; line-height: 1; }
  .brand-sub { font-weight: 400; letter-spacing: 1px; line-height: 1; }

  .card-front .brand { right: 105px; top: 60px; }
  .card-front .brand-mark { width: 46px; height: 46px; }
  .card-front .brand-name { font-size: 44px; color: var(--ink); }
  .card-front .brand-sub { font-size: 32px; color: var(--ink); margin-top: 14px; }

  .contact-list {
    position: absolute;
    right: 276px;
    top: 252px;
    list-style: none;
    color: var(--white);
    font-size: 14.5px;
    line-height: 25px;
    text-align: right;
  }
  .contact-list li { display: flex; justify-content: flex-end; align-items: center; gap: 8px; white-space: nowrap; }
  .contact-list .contact-email { font-size: 12.5px; }
  .contact-icon { width: 12px; height: 12px; flex: none; }
  .social-square { width: 11px; height: 11px; background: var(--white); border-radius: 2px; flex: none; }

  .owner { position: absolute; left: 352px; top: 244px; color: var(--white); }
  .owner-name { font-size: 21px; font-weight: 700; margin-bottom: 12px; }
  .owner-address { font-size: 15px; line-height: 25px; }

  .appointment-title {
    position: absolute; top: 36px; left: 0; right: 0;
    text-align: center; color: var(--red);
    font-size: 20px; font-weight: 600;
  }
  .appointment-row {
    position: absolute; left: 95px; display: flex; align-items: flex-end;
    color: var(--red); font-size: 14px; font-weight: 600;
  }
  .appointment-row.date { top: 104px; }
  .appointment-row.time { top: 142px; }
  .field-label { width: 60px; }
  .fill-line { border-bottom: 2px dotted var(--black); height: 12px; margin-bottom: 4px; }
  .date .fill-line { width: 317px; }
  .time .fill-line.am { width: 123px; margin-right: 12px; }
  .time .fill-line.pm { width: 128px; margin-left: 9px; margin-right: 2px; }

  .services {
    position: absolute; top: 174px; left: 30px; right: 30px;
    text-align: center; color: var(--muted);
    font-size: 11px; line-height: 15px;
  }
  .services-label { color: var(--red); font-weight: 600; }

  .back-band {
    position: absolute; left: 0; right: 0; bottom: 0; height: 141px;
    background: var(--red);
  }
  .card-back .brand { right: 155px; top: 247px; }
  .card-back .brand-mark {
    width: 32px; height: 32px; background: var(--white);
    box-shadow: inset 0 0 0 2px var(--white), inset 0 0 0 4px var(--red);
  }
  .card-back .brand-name { font-size: 31px; color: var(--white); }
  .card-back .brand-sub { font-size: 22px; color: var(--white); margin-top: 8px; }
</style>
</head>
<body>

<section class="card card-front" aria-label="Business card front">
  <svg class="front-shapes" width="587" height="362" viewBox="0 0 587 362" aria-hidden="true">
    <polygon points="0,198 401,198 381,223 0,223" fill="var(--black)"/>
    <polygon points="412,190 587,190 587,362 0,362 0,228 377,228" fill="var(--red)"/>
  </svg>

  <div class="brand">
    <div class="brand-row">
      <span class="brand-mark"></span>
      <span class="brand-name">BRIGHT CREST</span>
    </div>
    <span class="brand-sub">Detailing</span>
  </div>

  <ul class="contact-list">
    <li>call/text- 717-555-0148
      <svg class="contact-icon" viewBox="0 0 24 24" aria-hidden="true"><path fill="#fff" d="M6.6 10.8c1.4 2.8 3.8 5.1 6.6 6.6l2.2-2.2c.3-.3.7-.4 1-.2 1.1.4 2.3.6 3.6.6.6 0 1 .4 1 1V20c0 .6-.4 1-1 1C10.6 21 3 13.4 3 4c0-.6.4-1 1-1h3.5c.6 0 1 .4 1 1 0 1.3.2 2.5.6 3.6.1.3 0 .7-.2 1z"/></svg>
    </li>
    <li class="contact-email">brightcrestdetails@maildrop-example.com
      <svg class="contact-icon" viewBox="0 0 24 24" aria-hidden="true"><rect x="2" y="5" width="20" height="14" fill="#fff"/><path d="M3 6l9 7 9-7" fill="none" stroke="#e01f26" stroke-width="1.8"/></svg>
    </li>
    <li>@brightcrestdetailing <span class="social-square"></span></li>
  </ul>

  <div class="owner">
    <p class="owner-name">Mira Tolland</p>
    <p class="owner-address">4175 Quenhollow Rd<br>Ashmere PA 17492</p>
  </div>
</section>

<section class="card card-back" aria-label="Appointment card back">
  <h2 class="appointment-title">Your Next Appointment is</h2>
  <div class="appointment-row date">
    <span class="field-label">Date :</span>
    <span class="fill-line"></span>
  </div>
  <div class="appointment-row time">
    <span class="field-label">Time:</span>
    <span class="fill-line am"></span>AM
    <span class="fill-line pm"></span>PM
  </div>
  <p class="services"><span class="services-label">Minor Paint Correction:</span> Clay Barring · Multi-Step Buffing &amp; Polishing · Waxing<br>Hand Washes · Interior Cleaning · and More</p>
  <div class="back-band"></div>
  <div class="brand">
    <div class="brand-row">
      <span class="brand-mark"></span>
      <span class="brand-name">BRIGHT CREST</span>
    </div>
    <span class="brand-sub">Detailing</span>
  </div>
</section>

</body>
</html>
```